Healthy Sweets Manufacturer Needs Series of Card

We need a catchy series of cards (business card size) for display with our super healthy range of sweets in cafe cake cabinets. We are thinking maybe a groovy bean cartoon in different poses (since our cakes are made from white kidney beans) eg. Bean holding dumbells promoting High Protein, Skinny Bean promoting Low Calorie etc etc. Other cards to illustrate: Coconut oil, Low calorie, Low sugar, All natural, Superfood Ingredients, 'Made from Beans', Diabetic Friendly, Low GI, High Protein, Super Healthy, Dairy Free. Also 1 generic card that displays the name of product for sale. We have approx. 12 product lines for sale. Our logo is attached. Our target market is broad - anyone who loves cake. We really want to push the healthy aspects of our product and keep it fun and inviting.
Business Card Size. We would like you to create a fun bean character that presents in different poses on each card.
eg.
Card 1 - Bean character holding dumbells looking strong.
Card 2 - Bean character with sweatband like its been working out.
Card 3 - 'Skinny' Bean character like its slimmed right down
Card 4 - Bean character doing a one handed pushup.
Card 5 - Svelte looking bean character with lovely lashes and lipstick etc
Card 6 - A bean character with bulging muscles
Card 7 - An organic bean character
Card 8 - An athletic bean character.
Card 9 - An active bean character
Card 10 - A bean character with bikinis looking good.
Overall, these characters are to appear 'active' and 'healthy' as this is the message we are trying to get across.
All of these cards will be overlayed with health messages about our products such as "High Protein - Low Carbs", "Low to No Sugar", "Coconut Oil - The Good Fat", "The Healthy Treat" etc etc.
Updates
Project Deadline Extended
Reason: To All the designers that I have contacted, please submit the rest of your drawings. Thankyou.
Target Market(s)
Anyone who loves cake.
Industry/Entity Type
Business
Look and feel
Each slider illustrates characteristics of the customer's brand and the style your logo design should communicate.

```html
<!DOCTYPE html>
<html lang="en">
<head>
<meta charset="utf-8">
<title>Beanly Cafe Display Cards</title>
<link rel="stylesheet" href="https://fonts.googleapis.com/css2?family=Source+Sans+3:wght@400;600&display=swap">
<style>
  :root {
    --backdrop: #5e605e;
    --card-white: #ffffff;
    --orange: #fdb924;
    --orange-soft: #fde3a4;
    --green: #c2d42f;
    --green-soft: #e6eea6;
    --shadow-green: #9aa82a;
    --shadow-orange: #d9a032;
    --ink: #3d3d3d;
    --brand: #b5cb2a;
  }
  html, body {
    margin: 0;
    padding: 0;
    width: 1200px;
    height: 1000px;
    overflow: hidden;
    background: var(--backdrop);
  }
  body {
    position: relative;
    font-family: "Source Sans 3", Arial, sans-serif;
  }
  .card {
    position: absolute;
    width: 522px;
    height: 298px;
    background: var(--card-white);
    overflow: hidden;
  }
  .card--protein-cake  { left: 45px;  top: 145px; }
  .card--high-protein  { left: 633px; top: 145px; }
  .card--super-healthy { left: 45px;  top: 556px; }
  .card--low-sugar     { left: 633px; top: 556px; }

  .card__art {
    position: absolute;
    inset: 0;
    width: 100%;
    height: 100%;
  }
  .card--orange .card__field { fill: var(--orange); }
  .card--green .card__field  { fill: var(--green); }

  .brand {
    position: absolute;
    left: 38px;
    top: 36px;
    margin: 0;
    font-size: 46px;
    font-weight: 600;
    line-height: 1;
    letter-spacing: -0.5px;
    color: var(--brand);
  }
  .message {
    position: absolute;
    left: 37px;
    top: 137px;
    margin: 0;
    font-size: 21px;
    font-weight: 400;
    line-height: 24px;
    letter-spacing: -0.3px;
    color: var(--ink);
  }
  .message--right {
    left: auto;
    right: 37px;
    text-align: right;
    color: var(--card-white);
  }
</style>
</head>
<body>

  <section class="card card--orange card--protein-cake">
    <svg class="card__art" viewBox="0 0 544 310" preserveAspectRatio="none" aria-hidden="true">
      <path class="card__field" d="M225 0 Q312 155 255 310 L544 310 L544 0 Z"/>
    </svg>
    <p class="brand">Beanly</p>
    <p class="message">Grain Free. Gluten Free.<br>Sweetened with Stevia.<br>Made from Beans.</p>
    <p class="message message--right">Super Nutritions.<br>Superbly Delicious.<br>The ‘Healthy’ Cake</p>
  </section>

  <section class="card card--green card--high-protein">
    <svg class="card__art" viewBox="0 0 544 310" preserveAspectRatio="none">
      <defs>
        <radialGradient id="glow-protein" cx="50%" cy="45%" r="50%">
          <stop offset="0" stop-color="#ffffff"/>
          <stop offset="0.45" stop-color="#fcd37a"/>
          <stop offset="0.8" stop-color="var(--green-soft)"/>
          <stop offset="1" stop-color="var(--green)"/>
        </radialGradient>
      </defs>
      <path class="card__field" d="M225 0 Q312 155 253 310 L544 310 L544 0 Z"/>
      <ellipse role="img" aria-label="Cartoon white bean character in an orange singlet lifting dumbbells, standing on a soft shadow"
               cx="404" cy="144" rx="116" ry="126" fill="url(#glow-protein)"/>
    </svg>
    <p class="brand">Beanly</p>
    <p class="message">High Protein<br>Low Carbs</p>
  </section>

  <section class="card card--green card--super-healthy">
    <svg class="card__art" viewBox="0 0 544 310" preserveAspectRatio="none">
      <defs>
        <radialGradient id="glow-healthy" cx="50%" cy="45%" r="50%">
          <stop offset="0" stop-color="#ffffff"/>
          <stop offset="0.45" stop-color="#f6d88c"/>
          <stop offset="0.8" stop-color="var(--green-soft)"/>
          <stop offset="1" stop-color="var(--green)"/>
        </radialGradient>
      </defs>
      <path class="card__field" d="M225 0 Q312 155 255 310 L544 310 L544 0 Z"/>
      <ellipse role="img" aria-label="Cartoon white bean character with a sweatband and towel after a workout, beside a water bottle"
               cx="404" cy="160" rx="120" ry="116" fill="url(#glow-healthy)"/>
    </svg>
    <p class="brand">Beanly</p>
    <p class="message">Super Healthy</p>
  </section>

  <section class="card card--orange card--low-sugar">
    <svg class="card__art" viewBox="0 0 544 310" preserveAspectRatio="none">
      <defs>
        <radialGradient id="glow-sugar" cx="50%" cy="45%" r="50%">
          <stop offset="0" stop-color="#ffffff"/>
          <stop offset="0.45" stop-color="#dbe57a"/>
          <stop offset="0.8" stop-color="var(--orange-soft)"/>
          <stop offset="1" stop-color="var(--orange)"/>
        </radialGradient>
      </defs>
      <path class="card__field" d="M225 0 Q312 155 253 310 L544 310 L544 0 Z"/>
      <ellipse role="img" aria-label="Slim cartoon bean character dancing with a measuring tape around its waist"
               cx="404" cy="157" rx="106" ry="118" fill="url(#glow-sugar)"/>
    </svg>
    <p class="brand">Beanly</p>
    <p class="message">Low to No Sugar</p>
  </section>

</body>
</html>
```